Pull Up Banner - Recruitment Company

We would like a design for a pull up banner.

For context: we are a recruitment business. We specialise in helping people in healthcare industry to find jobs in Australia.

I have come up with several ideas and text for the banner. Feel free to use the following as you see appropriate:

- Our logo (see attached)
- 'Healthcare Recruitment Agency'
- Some sort of imagine / cartoon of medical professionals (ie. doctor, nurse, physiotherapist, speech pathologist). A cartoon is more friendly than committing to a photo
- 'Empowering your next career move'
- 'Discover tailored opportunities based on your career preferences'
- Dot points (allied health, nursing, medical imaging)
- Contact info at the bottom including our website (www.quellastaffing.com.au, our Instagram handle @quellastaffing, Mobile: XXXX XXX XXX. The title section for contact information could be 'Get in touch:'

Feel free to submit a couple of designs and we can merge aspects that look good on your designs and find the perfect fit.
Thank you
Updates

Hello,

Thank you for your initial submissions to this project. I appreciate the time you've invested.

After reviewing the first attempt, I'd like to share some feedback and initial observations:

- Professionalism and engagement: Is the overall appearance of the banner professional? It's crucial that we have a high-quality design as this will represent our business.

- Image selection: The image (whether cartoon or real people) appears quite generic. Please consider submitting the banner with a few different photos in the middle for us to choose from. Ensure the image is a good fit and not simply a generic stock photo.

- Contact section: Kindly remove the phone number; we no longer wish to include it on the banner. Instead, please include our website (www.quellastaffing.com.au) and Instagram handle (@quellastaffing).

- Color scheme: White, black, and red/pink are preferred, or alternatively, blue. However, please avoid incorporating too many different colors as it may detract from the professional appearance.

We will be printing the design on a banner and require it to look professional and engaging.

Thank you once again for your submissions. I hope the feedback provided above is helpful.

Warm regards,

Target Market(s)

Allied Health Australia

Font styles to use
Serif

Colors
0054AA
0677BA
7BADD7
CADEEF
E8F1F8
0094D4
00A9DD
6FCCEA
C7EBF8
E9F6FB
EB3D1F
EC4F4E
F09395
F8D3D4
FCEDEE

```html
<!DOCTYPE html>
<html lang="en">
<head>
<meta charset="utf-8">
<title>Quella Staffing – Pull Up Banner</title>
<link rel="stylesheet" href="https://fonts.googleapis.com/css2?family=Anton&family=Poppins:wght@500;600;700&display=swap">
<style>
  :root {
    --brand-blue: #2430c8;
    --ink: #0c0c0c;
    --paper: #ffffff;
    --footer-bg: #1c1c1c;
    --stage: #e6e6e6;
    --art-a: #cfd3f4;
    --art-b: #f6e6b0;
  }
  * { margin: 0; padding: 0; box-sizing: border-box; }
  html, body { width: 1090px; height: 1200px; overflow: hidden; background: var(--stage); }
  .banner {
    position: absolute; left: 308px; top: 20px;
    width: 474px; height: 1160px;
    background: var(--paper);
    font-family: "Poppins", sans-serif;
    text-align: center;
  }
  .block { position: absolute; left: 0; width: 100%; }
  .brand-name {
    top: 60px; font-weight: 700; font-size: 30px;
    letter-spacing: 4px; color: var(--ink); line-height: 1;
  }
  .headline { top: 140px; font-family: "Anton", sans-serif; line-height: 1; }
  .headline span { display: block; font-size: 58px; height: 58px; letter-spacing: 0.5px; }
  .headline .blue { color: var(--brand-blue); }
  .headline .black { color: var(--ink); }
  .dots { top: 324px; display: flex; justify-content: center; gap: 7px; }
  .dots i { width: 8px; height: 8px; border-radius: 50%; background: var(--ink); display: block; }
  .tagline { top: 340px; font-weight: 600; font-size: 18px; color: var(--brand-blue); }
  .artwork {
    top: 392px; left: 62px; width: 350px; height: 293px;
    background: linear-gradient(160deg, var(--art-a), var(--paper) 55%, var(--art-b));
    border-radius: 6px;
  }
  .kicker { top: 708px; font-weight: 500; font-size: 13px; letter-spacing: 2.4px; color: var(--ink); }
  .subhead { top: 726px; font-family: "Anton", sans-serif; font-size: 34px; line-height: 38px; }
  .subhead .black { color: var(--ink); display: block; }
  .subhead .blue { color: var(--brand-blue); display: block; }
  .side-bar { position: absolute; top: 822px; width: 35px; height: 109px; background: var(--brand-blue); }
  .side-bar.left { left: 0; }
  .side-bar.right { right: 0; }
  .sector {
    position: absolute; top: 822px; width: 110px; height: 109px;
    border: 2px solid var(--brand-blue);
    display: flex; align-items: center; justify-content: center;
    font-weight: 500; font-size: 20px; line-height: 1.2; color: var(--ink);
  }
  .contact {
    top: 945px; height: 189px; background: var(--footer-bg); color: var(--paper);
  }
  .contact h2 {
    font-family: "Anton", sans-serif; font-weight: 400; font-size: 36px;
    color: var(--brand-blue); margin-top: 18px; line-height: 1.1;
  }
  .contact-row { display: flex; align-items: center; justify-content: center; gap: 8px; }
  .phone { font-family: "Anton", sans-serif; font-size: 28px; margin-top: 6px; }
  .web, .social { font-weight: 600; font-size: 17px; margin-top: 4px; }
  .icon-dot { width: 18px; height: 18px; border-radius: 50%; background: var(--brand-blue); display: inline-block; }
</style>
</head>
<body>
<main class="banner">
  <div class="block brand-name">QUELLA STAFFING</div>

  <h1 class="block headline">
    <span class="blue">HEALTHCARE</span>
    <span class="black">RECRUITMENT</span>
    <span class="blue">AGENCY</span>
  </h1>

  <div class="block dots"><i></i><i></i><i></i><i></i><i></i></div>
  <p class="block tagline">Empowering your next career move</p>

  <div class="block artwork" role="img" aria-label="Cartoon of medical professionals around a candidate file, magnifying glass, test tubes and leaves"></div>

  <p class="block kicker">DISCOVER TAILORED OPPORTUNITIES</p>
  <h2 class="block subhead">
    <span class="black">BASED ON YOUR</span>
    <span class="blue">CAREER PREFERENCES</span>
  </h2>

  <div class="side-bar left"></div>
  <div class="sector" style="left:55px">Allied<br>health</div>
  <div class="sector" style="left:185px">Nursing</div>
  <div class="sector" style="left:312px">Medical</div>
  <div class="side-bar right"></div>

  <section class="block contact">
    <h2>GET IN TOUCH</h2>
    <div class="contact-row phone">
      <svg width="26" height="26" viewBox="0 0 26 26" aria-hidden="true">
        <circle cx="13" cy="13" r="13" fill="var(--brand-blue)"/>
        <path d="M8.5 7.5c1-.8 2-.6 2.5.4l1 2c.3.6.1 1.2-.4 1.6l-.8.6c.7 1.6 1.9 2.8 3.5 3.5l.6-.8c.4-.5 1-.7 1.6-.4l2 1c1 .5 1.2 1.5.4 2.5-1 1.2-2.6 1.4-4.2.6-2.8-1.3-5-3.5-6.3-6.3-.8-1.6-.6-3.2.6-4.2z" fill="#fff"/>
      </svg>
      <span>9123 480 275</span>
    </div>
    <div class="contact-row web">
      <svg width="18" height="18" viewBox="0 0 18 18" aria-hidden="true">
        <circle cx="9" cy="9" r="9" fill="var(--brand-blue)"/>
        <g fill="none" stroke="#fff" stroke-width="1.1">
          <circle cx="9" cy="9" r="5.5"/><ellipse cx="9" cy="9" rx="2.4" ry="5.5"/>
          <line x1="3.5" y1="9" x2="14.5" y2="9"/>
        </g>
      </svg>
      <span>www.quellastaffing.com.au</span>
    </div>
    <div class="contact-row social">
      <span class="icon-dot"></span>
      <span>@quellastaffing</span>
    </div>
  </section>
</main>
</body>
</html>
```